Call Center In Need of Website Design

We are a call center that provides inbound and outbound calling & marketing services for eCommerce store. We would like to see a fun, creative, playful design that is simple.

Here are some sample design sites we like;
- https://www.velmoreline.com/
- https://pindrask.io/
- https://www.glimbertic.com/live-chat-software/
- https://www.zavrolin.com/

Here are some competitor sites;
- https://www.ostrevaglinks.com/
- https://www.helpkestrel.com/

I have attached website content for your use.

Target Market(s)

eCommerce

Coding

Coded - Design and coding required

Number of Pages Required

5+ page

Font styles to use
Sans Serif

Colors

Designer to choose colors to be used in the design.

Requirements
Must have
• Must have designs for the following 5 separate pages;
• 1. Home (landing)
• - This will be were the design style really needs to show.
• - Just needs to touch on key services
• - CTA
• 2. About Us
• - Basic page for about me paragraph
• 3. Services
• - List of services with icons
• - Click on service type to expand details or hover over service icon to view popup bubble with details about that service
• 4. Pricing
• - Option to bundle 1(one) digital service plan and 1(one) call center service plan
• - Bundling adds 10% monthly discount to over all price
• - Customer does NOT have to bundle
• - FAQ
• 5. Contact Us
• - Include a capture form (name, company name, email, phone, message)
• - Contact info
• - Business hours
• When customer purchases their desired plan, then they are taken to a page where they must schedule a call with an account rep.
Nice to have
• home page animations
Should not have
• All information on Home/Landing page.

```html
<!DOCTYPE html>
<html lang="en">
<head>
<meta charset="utf-8">
<title>Orbivo – Omnichannel Customer Care</title>
<link href="https://fonts.googleapis.com/css2?family=Mulish:wght@400;600;700;800&display=swap" rel="stylesheet">
<style>
:root{
  --navy:#34347f;
  --navy-dark:#2b2b6e;
  --teal:#67c5ad;
  --teal-light:#83d8c1;
  --field:#7fd3bc;
  --mint:#5fd1b2;
  --pale:#eef6f9;
  --ink:#2d2d5e;
  --body:#5e6470;
  --muted:#9aa0a8;
  --white:#ffffff;
  --stage:#ececee;
}
*{margin:0;padding:0;box-sizing:border-box}
html,body{width:1200px;height:2416px;overflow:hidden}
body{background:var(--stage);font-family:'Mulish',Arial,sans-serif;color:var(--body);position:relative}
.abs{position:absolute}

/* ---------- Desktop page ---------- */
.desktop{position:absolute;left:56px;top:40px;width:773px;height:1167px;background:var(--white);box-shadow:0 6px 24px rgba(0,0,0,.12);overflow:hidden}
.desktop section,.desktop footer{position:relative;width:100%}
.brand{color:var(--white);font-weight:600;letter-spacing:4px;white-space:nowrap}
.d-hero{height:362px;background:var(--navy)}
.d-hero .brand{left:105px;top:26px;font-size:24px;line-height:30px;color:var(--white)}
.d-nav{left:362px;top:36px;display:flex;gap:22px;font-size:7px;line-height:10px;font-weight:700;letter-spacing:.6px;color:#c9c9e6;text-transform:uppercase;white-space:nowrap}
.d-nav .active{color:var(--white)}
.d-hero h1{left:103px;top:138px;font-size:22px;line-height:28px;font-weight:800;color:var(--white)}
.d-hero .tagline{left:103px;top:206px;font-size:12px;color:#dedef3}
.hero-links{display:flex;gap:14px;font-size:7.5px;font-weight:800;color:var(--white);text-transform:uppercase}
.hero-links span{border-bottom:1.5px solid var(--white);padding-bottom:2px}
.d-hero .hero-links{left:103px;top:246px}
.hero-art{background:radial-gradient(circle at 50% 55%,#ec6a66 0 18%,#5b5bb0 19% 48%,transparent 62%),linear-gradient(160deg,#4a4a99,#3b3b88);border-radius:50%}
.d-hero .hero-art{left:440px;top:90px;width:215px;height:215px}

.d-services{height:206px;background:var(--teal)}
.svc-card{width:124px;height:132px;background:var(--white);border-radius:4px;overflow:hidden}
.svc-card .icon-area{height:74px;background:var(--navy);display:flex;align-items:center;justify-content:center}
.svc-card .icon-area i{display:block;width:36px;height:36px;border-radius:50%;background:#4b4b99}
.svc-card h3{margin:12px 0 0 10px;font-size:8px;font-weight:800;color:var(--ink)}
.svc-card h3::before{content:"";display:inline-block;width:3px;height:3px;background:var(--ink);border-radius:50%;margin-right:5px;vertical-align:middle}
.svc-card p{margin:3px 0 0 10px;font-size:6.5px;line-height:9px;color:var(--muted)}
.d-services .card-a{left:110px;top:37px}
.d-services .card-b{left:241px;top:37px}
.what-we-do h2{font-size:11px;font-weight:700;color:var(--white)}
.what-we-do h2::after{content:"";display:block;width:22px;height:1.5px;background:var(--white);margin-top:6px}
.what-we-do p{font-size:6.6px;line-height:11px;color:var(--white);margin-top:10px}
.btn-outline{display:inline-block;border:1.5px solid var(--white);border-radius:3px;color:var(--white);font-weight:800}
.d-services .what-we-do{left:386px;top:41px;width:280px}
.d-services .btn-outline{margin-top:12px;font-size:7px;padding:7px 14px}

.d-faq{height:317px;background:var(--pale)}
.faq-title{width:100%;text-align:center;font-weight:800;color:var(--navy)}
.faq-title::after{content:"";display:block;width:26px;height:1.5px;background:var(--navy);margin:7px auto 0}
.d-faq .faq-title{top:42px;font-size:18px}
.faq-sub{width:100%;text-align:center;color:var(--body)}
.d-faq .faq-sub{top:87px;font-size:7.5px}
.faq-card{background:var(--white);box-shadow:0 4px 14px rgba(0,0,0,.12)}
.faq-card .quote{color:#e8ecef;font-weight:800;font-family:Georgia,serif;line-height:1}
.faq-card .answer{color:var(--body)}
.faq-card .question{color:var(--ink);font-weight:800}
.faq-card .brand{color:var(--ink);font-weight:600}
.d-faq .faq-card{left:145px;top:120px;width:483px;height:122px}
.d-faq .quote{left:16px;top:2px;font-size:70px}
.d-faq .answer{left:80px;top:20px;width:360px;font-size:7px;line-height:11px}
.d-faq .question{left:80px;top:82px;font-size:7.5px}
.d-faq .faq-card .brand{left:280px;top:70px;font-size:22px;letter-spacing:4px}
.dots{display:flex;gap:4px;align-items:center}
.dots i{width:3px;height:3px;border-radius:50%;background:var(--ink);display:block}
.dots i:first-child{width:5px;height:5px;background:var(--mint)}
.d-faq .dots{left:362px;top:259px}
.d-faq .arrow-l{left:148px;top:254px}
.d-faq .arrow-r{left:610px;top:254px}

.d-contact{height:217px;background:var(--teal)}
.contact-box{background:var(--teal-light)}
.contact-box h4{color:var(--white);font-weight:800}
.contact-box h4::after{content:"";display:block;width:20px;height:1.5px;background:var(--white);margin-top:5px}
.contact-box li{list-style:none;display:flex;gap:7px;color:var(--white)}
.contact-box svg{flex:none}
.d-contact .contact-box{left:121px;top:35px;width:177px;height:160px;padding:18px 14px}
.d-contact h4{font-size:8px;margin-bottom:16px}
.d-contact li{font-size:6.5px;line-height:9px;margin-bottom:8px}
.callback h2{color:var(--white);font-weight:700}
.field{background:var(--field);color:var(--white);display:flex;align-items:center}
.btn-submit{border:1.5px solid var(--white);border-radius:3px;color:var(--white);font-weight:800;display:inline-flex;align-items:center;justify-content:center}
.d-contact .callback{left:314px;top:32px;width:340px}
.d-contact .callback h2{font-size:17px;margin-bottom:16px}
.d-grid{display:grid;grid-template-columns:163px 163px;gap:9px 14px}
.d-contact .field{height:24px;font-size:6.5px;padding-left:8px}
.d-contact .btn-submit{margin-top:16px;width:68px;height:24px;font-size:6.5px}

.d-footer{height:65px;background:var(--white)}
.d-footer .copy{left:103px;top:22px;font-size:7px;line-height:11px;color:var(--body)}
.foot-nav{display:flex;color:var(--body)}
.foot-nav .active{color:var(--mint)}
.d-footer .foot-nav{left:320px;top:27px;gap:18px;font-size:7.5px}
.social{display:flex;gap:3px}
.social i{display:block;background:var(--navy);border-radius:1px}
.d-footer .social{left:590px;top:25px}
.d-footer .social i{width:14px;height:14px}

/* ---------- Mobile page ---------- */
.mobile{position:absolute;left:887px;top:126px;width:261px;height:2148px;background:var(--white);box-shadow:0 6px 24px rgba(0,0,0,.12);overflow:hidden}
.mobile section,.mobile footer{position:relative;width:100%}
.m-hero{height:551px;background:var(--navy)}
.m-hero .brand{left:14px;top:24px;font-size:22px}
.burger{right:12px;top:78px;width:14px}
.burger i{display:block;height:1.5px;background:var(--white);margin-bottom:3px}
.burger i:nth-child(2){margin-left:3px}
.m-hero h1{left:12px;top:132px;font-size:21px;line-height:27px;font-weight:800;color:var(--white)}
.m-hero .tagline{left:12px;top:200px;font-size:11px;color:#dedef3}
.m-hero .hero-links{left:12px;top:244px;font-size:7px}
.m-hero .hero-art{left:16px;top:280px;width:230px;height:230px}

.m-services{height:544px;background:var(--teal)}
.m-services .svc-card{width:129px;height:138px;left:68px}
.m-services .card-a{top:31px}
.m-services .card-b{top:190px}
.m-services .svc-card .icon-area{height:80px}
.m-services .what-we-do{left:10px;top:362px;width:240px}
.m-services .what-we-do p{font-size:7px;line-height:12px}
.m-services .btn-outline{margin-top:14px;font-size:7px;padding:7px 12px}

.m-faq{height:402px;background:var(--pale)}
.m-faq .faq-title{top:42px;font-size:16px}
.m-faq .faq-sub{top:86px;font-size:7px;white-space:nowrap}
.m-faq .faq-card{left:10px;top:124px;width:240px;height:201px}
.m-faq .quote{left:8px;top:4px;font-size:56px}
.m-faq .answer{left:22px;top:24px;width:205px;font-size:7.5px;line-height:12px}
.m-faq .question{left:22px;top:108px;font-size:7.5px}
.m-faq .faq-card .brand{left:70px;top:136px;font-size:21px;letter-spacing:4px}
.m-faq .dots{left:112px;top:362px}
.m-faq .arrow-l{left:14px;top:356px}
.m-faq .arrow-r{left:232px;top:356px}

.m-contact{height:470px;background:var(--teal)}
.m-contact .contact-box{left:35px;top:35px;width:192px;height:169px;padding:18px 16px}
.m-contact h4{font-size:8px;margin-bottom:16px}
.m-contact li{font-size:6.5px;line-height:9px;margin-bottom:9px}
.m-contact .callback{left:0;top:226px;width:100%;text-align:center}
.m-contact .callback h2{font-size:15px;margin-bottom:14px}
.m-stack{display:flex;flex-direction:column;gap:12px;align-items:center}
.m-contact .field{width:177px;height:26px;font-size:6.5px;padding-left:10px}
.m-contact .btn-submit{margin-top:12px;width:72px;height:26px;font-size:6.5px;margin-left:43px;align-self:flex-start}

.m-footer{height:180px;background:var(--white);text-align:center}
.m-footer .copy{top:18px;width:100%;font-size:7px;color:var(--body)}
.m-footer .foot-nav{flex-direction:column;top:40px;width:100%;font-size:7.5px;line-height:15px}
.m-footer .social{left:101px;top:148px}
.m-footer .social i{width:14px;height:14px}
</style>
</head>
<body>

<main class="desktop">
  <section class="d-hero">
    <div class="abs brand">ORBIVO</div>
    <nav class="abs d-nav"><span class="active">Home</span><span>About Us</span><span>Services</span><span>Pricing</span><span>Contact Us</span><span>Account</span></nav>
    <h1 class="abs">Orbivo Is An<br>Omnichannel</h1>
    <p class="abs tagline">Provider For Customer Care</p>
    <div class="abs hero-links"><span>Learn More</span><span>Get Started</span></div>
    <div class="abs hero-art" role="img" aria-label="Illustration of a laptop, tablet and phone surrounded by chat and media icons"></div>
  </section>

  <section class="d-services">
    <article class="abs svc-card card-a">
      <div class="icon-area" role="img" aria-label="Digital services icon"><i></i></div>
      <h3>Digital Services</h3>
      <p>Email Support<br>Live Chat Support</p>
    </article>
    <article class="abs svc-card card-b">
      <div class="icon-area" role="img" aria-label="Call center services icon"><i></i></div>
      <h3>Call Center Services</h3>
      <p>Answering service<br>Welcome Calls</p>
    </article>
    <div class="abs what-we-do">
      <h2>What We Do</h2>
      <p>Orbivo is your personal customer service and product research team. We love eCommerce, but we love seeing business owners succeed even more! That is exactly why we have developed the processes and technology to take care of the most over looked areas in eCommerce - Customer Service and Retention.</p>
      <span class="btn-outline">More</span>
    </div>
  </section>

  <section class="d-faq">
    <h2 class="abs faq-title">Frequently Asked Quetions</h2>
    <p class="abs faq-sub">Lorem Ipsum Dolor Sit Amet Consectetor Lorem Ipsum Dolor Sit Amet Consectetor</p>
    <div class="abs faq-card">
      <span class="abs quote">&ldquo;</span>
      <p class="abs answer">The free trial only relates to the "call center" service packages! There is no hidden fine print or fees to get started. We don't even require any payment info, signatures, or deposits. If you don't like us or our service, just simply walk away.</p>
      <p class="abs question">Is the free trial really free?</p>
      <span class="abs brand">ORBIVO</span>
    </div>
    <svg class="abs arrow-l" width="14" height="10" viewBox="0 0 14 10"><path d="M13 5H1M5 1L1 5l4 4" fill="none" stroke="#6b6f78" stroke-width="1.2"/></svg>
    <div class="abs dots"><i></i><i></i><i></i><i></i><i></i></div>
    <svg class="abs arrow-r" width="14" height="10" viewBox="0 0 14 10"><path d="M1 5h12M9 1l4 4-4 4" fill="none" stroke="#6b6f78" stroke-width="1.2"/></svg>
  </section>

  <section class="d-contact">
    <div class="abs contact-box">
      <h4>Contact Details</h4>
      <ul>
        <li><svg width="8" height="8" viewBox="0 0 10 10"><path d="M2 1l2 2-1 1.5c.8 1.5 1.7 2.4 3 3L7.5 6l2 2-1.5 1.5C4.5 9 1 5.5.5 2z" fill="#fff"/></svg>Phone: (800) 555-0148</li>
        <li><svg width="8" height="8" viewBox="0 0 10 10"><rect x="0.5" y="2" width="9" height="6" fill="#fff"/><path d="M.5 2l4.5 3.5L9.5 2" fill="none" stroke="#83d8c1"/></svg>info@orbivo.co</li>
        <li><svg width="8" height="9" viewBox="0 0 8 10"><path d="M4 0a3.5 3.5 0 0 1 3.5 3.5C7.5 6 4 10 4 10S.5 6 .5 3.5A3.5 3.5 0 0 1 4 0z" fill="#fff"/><circle cx="4" cy="3.5" r="1.3" fill="#83d8c1"/></svg><span>Orbivo, Inc.<br>412 Larkmoor St, Delwyn, CA 90014</span></li>
      </ul>
    </div>
    <div class="abs callback">
      <h2>Request For Call Back</h2>
      <div class="d-grid">
        <div class="field">Name</div><div class="field">Email</div>
        <div class="field">Ph Num</div><div class="field">Enquiry About</div>
      </div>
      <span class="btn-submit">Submit Now</span>
    </div>
  </section>

  <footer class="d-footer">
    <p class="abs copy">Copyright © 2018.<br>All rights reserved</p>
    <nav class="abs foot-nav"><span class="active">Home</span><span>About Us</span><span>Service</span><span>Pricing</span><span>Contact Us</span><span>Account</span></nav>
    <div class="abs social"><i></i><i></i><i></i><i></i></div>
  </footer>
</main>

<main class="mobile">
  <section class="m-hero">
    <div class="abs brand">ORBIVO</div>
    <div class="abs burger"><i></i><i></i><i></i></div>
    <h1 class="abs">Orbivo Is An<br>Omnichannel</h1>
    <p class="abs tagline">Provider For Customer Care</p>
    <div class="abs hero-links"><span>Learn More</span><span>Get Started</span></div>
    <div class="abs hero-art" role="img" aria-label="Illustration of a laptop, tablet and phone surrounded by chat and media icons"></div>
  </section>

  <section class="m-services">
    <article class="abs svc-card card-a">
      <div class="icon-area" role="img" aria-label="Digital services icon"><i></i></div>
      <h3>Digital Services</h3>
      <p>Email Support<br>Live Chat Support</p>
    </article>
    <article class="abs svc-card card-b">
      <div class="icon-area" role="img" aria-label="Call center services icon"><i></i></div>
      <h3>Call Center Services</h3>
      <p>Answering service<br>Welcome Calls</p>
    </article>
    <div class="abs what-we-do">
      <h2>What We Do</h2>
      <p>Orbivo is your personal customer service and product research team. We love eCommerce, but we love seeing business owners succeed even more! That is exactly why we have developed the processes and technology to take care of the most over looked areas in eCommerce - Customer Service and Retention.</p>
      <span class="btn-outline">More</span>
    </div>
  </section>

  <section class="m-faq">
    <h2 class="abs faq-title">Frequently Asked Quetion</h2>
    <p class="abs faq-sub">Lorem Ipsum Dolor Sit Amet Consectetor Lorem Ipsum Dolor</p>
    <div class="abs faq-card">
      <span class="abs quote">&ldquo;</span>
      <p class="abs answer">The free trial only relates to the "call center" service packages! There is no hidden fine print or fees to get started. We don't even require any payment info, signatures, or deposits. If you don't like us or our service, just simply walk away.</p>
      <p class="abs question">Is the free trial really free?</p>
      <span class="abs brand">ORBIVO</span>
    </div>
    <svg class="abs arrow-l" width="14" height="10" viewBox="0 0 14 10"><path d="M13 5H1M5 1L1 5l4 4" fill="none" stroke="#6b6f78" stroke-width="1.2"/></svg>
    <div class="abs dots"><i></i><i></i><i></i><i></i><i></i></div>
    <svg class="abs arrow-r" width="14" height="10" viewBox="0 0 14 10"><path d="M1 5h12M9 1l4 4-4 4" fill="none" stroke="#6b6f78" stroke-width="1.2"/></svg>
  </section>

  <section class="m-contact">
    <div class="abs contact-box">
      <h4>Contact Details</h4>
      <ul>
        <li><svg width="8" height="8" viewBox="0 0 10 10"><path d="M2 1l2 2-1 1.5c.8 1.5 1.7 2.4 3 3L7.5 6l2 2-1.5 1.5C4.5 9 1 5.5.5 2z" fill="#fff"/></svg>Phone: (800) 555-0148</li>
        <li><svg width="8" height="8" viewBox="0 0 10 10"><rect x="0.5" y="2" width="9" height="6" fill="#fff"/><path d="M.5 2l4.5 3.5L9.5 2" fill="none" stroke="#83d8c1"/></svg>info@orbivo.co</li>
        <li><svg width="8" height="9" viewBox="0 0 8 10"><path d="M4 0a3.5 3.5 0 0 1 3.5 3.5C7.5 6 4 10 4 10S.5 6 .5 3.5A3.5 3.5 0 0 1 4 0z" fill="#fff"/><circle cx="4" cy="3.5" r="1.3" fill="#83d8c1"/></svg><span>Orbivo, Inc.<br>412 Larkmoor St, Delwyn, CA 90014</span></li>
      </ul>
    </div>
    <div class="abs callback">
      <h2>Request For Call Back</h2>
      <div class="m-stack">
        <div class="field">Name</div>
        <div class="field">Email</div>
        <div class="field">Phn No.</div>
        <div class="field">Enquiry About</div>
        <span class="btn-submit">Submit Now</span>
      </div>
    </div>
  </section>

  <footer class="m-footer">
    <p class="abs copy">Copyright © 2018. All rights reserved</p>
    <nav class="abs foot-nav"><span class="active">Home</span><span>About Us</span><span>Service</span><span>Pricing</span><span>Contact Us</span><span>Account</span></nav>
    <div class="abs social"><i></i><i></i><i></i><i></i></div>
  </footer>
</main>

</body>
</html>
```